Web Design for guards MMJ transport and security services

Harbor Crest Protective solutions a tallow unified company, is looking for a designer to create a website that displays our service portfolio. We need marketing pictures and content to be created in a original and competitive fashion, intriguing to our customers. We will need forms on the website to be created for calendar booking (somehow integrate into exchange if possible) and general inquiry forms. There will need to be pages dedicated to our staff, MMJ trasnport & Courier services, our vehicles, alarm systems, video systems, video monitoring, private investigations, and surveillance aduit and compliance investigations, payment gateway integration, and general company information. I Have attached our main company logo. Also have a emphasis on being state licensed by the Colorado RPB. Have a link to our parent site, tallowcctv.example

Target Market(s)

Colorado Marijuana industry, MMJ transport services, guard services, armed gaurd services.

Contact Information for Business Card

Would like a sleek simple design highlighting what we offer. must match the website and have a overall professional straight to the point appearance.

Number of Pages Required

1 page

Colors
33b8a4
00a990
9bcb3c
acd036
cadf82
85cae6
33a6d7
0792cd

Requirements
Must have
• Easy to use, lots of images, professional.
Nice to have
• Creativity

```html
<!DOCTYPE html>
<html lang="en">
<head>
<meta charset="utf-8">
<title>Harbor Crest Protective solutions</title>
<link href="https://fonts.googleapis.com/css2?family=Source+Sans+3:wght@400;600;700&display=swap" rel="stylesheet">
<style>
:root{
  --teal:#00a990;
  --green:#9bcb3c;
  --blue:#33a6d7;
  --blue-bar:#0aa0d8;
  --blue-deep:#0792cd;
  --red:#d9262c;
  --ink:#333;
  --muted:#666;
  --rule:#e2e2e2;
  --band-a:#ececec;
  --band-b:#f4f4f4;
  --footer:#2c2e3a;
  --footer-text:#c9ccd6;
  --field:#d9dbe0;
}
*{box-sizing:border-box;margin:0;padding:0}
html,body{width:1200px;height:2225px;overflow:hidden}
body{position:relative;font-family:"Source Sans 3",sans-serif;color:var(--ink);background:#fff}
.abs{position:absolute}
a{color:inherit;text-decoration:none}

/* header */
.brand{left:132px;top:20px;width:170px;height:110px;display:flex;flex-direction:column;align-items:center;justify-content:center;gap:8px}
.brand-mark{width:46px;height:46px;border-radius:50%;background:var(--red)}
.brand-name{font-size:21px;font-weight:700;color:var(--red);white-space:nowrap}
.top-contact{right:134px;top:37px;display:flex;align-items:center;gap:14px;font-size:13.5px;color:var(--ink)}
.top-contact span{display:flex;align-items:center;gap:6px}
.top-contact .sep{width:1px;height:16px;background:#ccc}
.main-nav{left:647px;top:96px;height:48px;display:flex;align-items:center;font-size:13px;text-transform:uppercase;color:#555}
.main-nav a{margin-right:26px}
.main-nav .current{color:var(--red);text-decoration:underline;text-underline-offset:4px}
.main-nav .services{margin:0;background:var(--blue-deep);color:#fff;height:48px;width:106px;display:flex;align-items:center;justify-content:center;margin-left:-2px}
.sub-nav{left:0;top:144px;width:1200px;height:40px;background:var(--blue-bar)}
.sub-nav ul{list-style:none;position:absolute;left:132px;top:0;height:40px;display:flex;font-size:12.5px;font-weight:600;color:#fff}
.sub-nav li{display:flex;align-items:center;padding:0 9px}
.sub-nav li.active{background:var(--blue-deep);padding:0 10px}

/* hero */
.hero{left:0;top:184px;width:1200px;height:429px;background:linear-gradient(100deg,#2d3a4a 0%,#a9674a 22%,#4a5a6d 40%,#e6e6e6 52%,#c8323a 70%,#8e1f25 85%,#3c4656 100%)}
.dots{left:571px;top:582px;display:flex;gap:7px}
.dots i{width:8px;height:8px;border-radius:50%;background:#fff;opacity:.7}
.dots i:first-child{opacity:1;background:#bbb;border:1px solid #fff}

/* welcome */
.welcome{left:132px;top:650px;width:934px;text-align:center}
.welcome h1{font-size:31px;font-weight:400;color:var(--teal)}
.welcome h2{font-size:17px;font-weight:600;color:#222;margin-top:4px}
.welcome p{font-size:10.5px;line-height:20px;color:var(--muted);margin-top:10px;text-align:justify;text-align-last:center}
.rule{left:132px;width:934px;height:1px;background:var(--rule)}

/* services */
.service{top:872px;width:440px;height:110px}
.service .icon{position:absolute;left:0;top:5px;width:90px;height:90px;border-radius:50%;display:flex;align-items:center;justify-content:center}
.service h3{position:absolute;left:98px;top:0;font-size:31px;font-weight:400}
.service p{position:absolute;left:98px;top:46px;width:340px;font-size:10.5px;line-height:19.5px;color:var(--muted);text-align:justify}
.service p b{color:#222;font-weight:600}
.transport .icon{background:var(--teal)}
.transport h3{color:var(--teal)}
.security .icon{background:var(--green)}
.security h3{color:var(--green)}
.v-rule{left:599px;top:878px;width:1px;height:104px;background:var(--rule)}

/* galleries */
.gallery-head{top:1046px;width:437px;display:flex;align-items:center;font-size:20px;color:var(--blue)}
.gallery-head .more{margin-left:auto;font-size:22px}
.gallery-head .tab-off{color:#999;border-left:1px solid #ccc;padding-left:10px;margin-left:10px}
.thumbs{top:1090px;width:437px;display:grid;grid-template-columns:repeat(3,133px);justify-content:space-between;row-gap:20px}
.thumb{height:133px;position:relative}
.thumb .caption{position:absolute;left:0;right:0;bottom:0;height:24px;background:rgba(0,0,0,.45);color:#fff;font-size:11px;font-weight:600;display:flex;align-items:center;justify-content:center}
.t-truck{background:linear-gradient(160deg,#7e97b8,#c9c2b4 55%,#5b5f66)}
.t-truck2{background:linear-gradient(160deg,#d6a07a,#8fa1bf 55%,#4f5b6b)}
.t-truck3{background:linear-gradient(160deg,#a9c3dc,#dadde0 55%,#6f7a85)}
.t-truck4{background:linear-gradient(160deg,#5c7a6e,#2f5a43 55%,#4a4f55)}
.t-truck5{background:linear-gradient(160deg,#9bb6d6,#3b5fa8 55%,#6c6f78)}
.t-truck6{background:linear-gradient(160deg,#8fb4e0,#b9553f 55%,#77746c)}
.t-cam{background:linear-gradient(160deg,#f4f4f4,#cfd1d3 60%,#a9abad)}
.t-cam2{background:linear-gradient(160deg,#e8e8e8,#b7b9bb 60%,#8e9092)}
.t-cam3{background:linear-gradient(160deg,#bda98c,#e3e2de 60%,#8e8778)}
.t-cam4{background:linear-gradient(160deg,#606466,#b8bbbd 60%,#4a4d50)}
.t-cam5{background:linear-gradient(160deg,#c9d4de,#f1f1f1 60%,#a4b2bf)}

/* feature band */
.band{top:1434px;width:600px;height:240px}
.band-left{left:0;background:var(--band-a)}
.band-right{left:600px;background:var(--band-b)}
.feature h3{position:absolute;top:32px;font-size:22px;font-weight:400;color:var(--blue-deep)}
.feature .photo{position:absolute;top:74px;width:148px;height:131px}
.feature p{position:absolute;top:72px;width:274px;font-size:10.5px;line-height:19px;color:var(--muted);text-align:justify}
.feature p b{color:#222;font-weight:600}
.ph-courier{background:linear-gradient(150deg,#d7c8bd,#f1eeea 45%,#b9252b 80%)}
.ph-monitor{background:linear-gradient(150deg,#2f4560,#4f7fb0 45%,#1d2a3a)}

/* contact strip */
.badge-seal{left:132px;top:1700px;width:50px;height:50px;border-radius:50%;background:#2a2a2a;border:3px solid #c9a53c}
.partner{left:200px;top:1703px;display:flex;align-items:center;gap:8px;font-size:22px;font-weight:600;color:var(--blue-deep)}
.partner i{width:40px;height:40px;border-radius:50%;background:var(--blue)}
.contact-info{right:172px;top:1707px;text-align:right}
.contact-info .addr{font-size:11px;color:#222}
.contact-info .line{font-size:15.5px;color:#333;margin-top:6px}
.contact-info .line span{color:#aaa;margin:0 6px}
.phone-dot{left:1036px;top:1710px;width:30px;height:30px;border-radius:50%;background:#3c3c3c;display:flex;align-items:center;justify-content:center}

/* map */
.map{left:0;top:1780px;width:1200px;height:240px;background:linear-gradient(180deg,#e6e7e9,#d9dbde)}

/* footer */
.footer{left:0;top:2020px;width:1200px;height:205px;background:var(--footer)}
.f-title{font-size:12.5px;color:var(--blue)}
.f-nav{left:132px;top:2028px}
.f-nav .cols{display:flex;gap:0;margin-top:8px}
.f-nav ul{list-style:none;width:165px;font-size:9.5px;line-height:19.5px;color:var(--footer-text)}
.f-div{top:2045px;width:1px;height:150px;background:#474a58}
.f-contact{left:445px;top:2028px}
.f-form{left:446px;top:2080px;width:420px;height:110px}
.field{position:absolute;height:28px;background:var(--field);font-size:9px;color:#333;padding-left:14px;display:flex;align-items:center}
.submit{position:absolute;left:367px;top:79px;width:53px;height:28px;background:var(--blue-deep);color:#fff;font-size:9px;font-weight:600;display:flex;align-items:center;justify-content:center}
.copy{right:134px;top:2055px;text-align:right;font-size:9.5px;line-height:22px;color:var(--footer-text)}
.social{right:134px;top:2132px;display:flex;gap:8px}
.social i{width:24px;height:24px;border-radius:50%;background:#2f7fd0}
</style>
</head>
<body>

<header>
  <div class="abs brand"><span class="brand-mark"></span><span class="brand-name">Harbor Crest</span></div>
  <div class="abs top-contact">
    <span><svg width="12" height="12" viewBox="0 0 24 24"><path fill="#333" d="M6.6 10.8a15 15 0 0 0 6.6 6.6l2.2-2.2c.3-.3.7-.4 1-.2 1.1.4 2.3.6 3.6.6.6 0 1 .4 1 1V20c0 .6-.4 1-1 1A17 17 0 0 1 3 4c0-.6.4-1 1-1h3.5c.6 0 1 .4 1 1 0 1.3.2 2.5.6 3.6.1.3 0 .7-.2 1z"/></svg>555.010.2415</span>
    <span class="sep"></span>
    <span><svg width="13" height="11" viewBox="0 0 24 18"><path fill="#333" d="M0 0h24v2L12 10 0 2zM0 4l12 8 12-8v14H0z"/></svg>info@harborcrestprotective.example</span>
  </div>
  <nav class="abs main-nav">
    <a class="current">Home</a><a>About us</a><a>Our staff</a><a>Contact us</a><a class="services">Our services</a>
  </nav>
  <div class="abs sub-nav">
    <ul>
      <li class="active">MMJ trasnport &amp; Courier services</li><li>Our vehicles</li><li>Alarm systems</li><li>video systems</li><li>video monitoring</li><li>Private investigations</li><li>Surveillance audit</li><li>Compliance investigations</li>
    </ul>
  </div>
</header>

<div class="abs hero" role="img" aria-label="Red cargo truck at a container port with security cameras in the foreground"></div>
<div class="abs dots"><i></i><i></i><i></i><i></i></div>

<section class="abs welcome">
  <h1>Welcome to Harbor Crest Protective solutions</h1>
  <h2>Donec aliquam lorem in sem pretium, tristique porttitor massa facilisis</h2>
  <p>Aliquam ullamcorper nisi ex, et ultricies quam congue sit amet. Mauris placerat dui sed mauris tristique pharetra. Proin porttitor sem mi, sit amet pulvinar magna euismod sed. Donec condimentum eu justo sed auctor. Fusce non mattis odio, ac sollicitudin est. Duis at commodo libero, ut consectetur felis. Aliquam facilisis, metus a tincidunt dapibus, tortor magna bibendum eros, sed suscipit mauris turpis non lectus. Integer nec ligula non leo pulvinar commodo et eget elit. Mauris commodo augue odio, nec accumsan nisl maximus eget. Etiam quis magna nec odio sagittis pretium id eget risus. Integer luctus ultricies arcu, eget fermentum magna pulvinar et.</p>
</section>
<div class="abs rule" style="top:844px"></div>

<section class="abs service transport" style="left:132px">
  <div class="icon"><svg width="32" height="24" viewBox="0 0 32 24"><path fill="#fff" d="M2 3h18v14H2zM21 8h6l4 5v4h-10zM7 21a3 3 0 1 0 0-.1zM25 21a3 3 0 1 0 0-.1z"/></svg></div>
  <h3>Transport Service</h3>
  <p>Aliquam ullamcorper nisi ex, et ultricies quam congue sit amet. Mauris placerat dui sed mauris tristique pharetra. Proin porttitor sem mi, sit amet pulvinar magna euismod sed. <b>Read more</b></p>
</section>
<div class="abs v-rule"></div>
<section class="abs service security" style="left:630px">
  <div class="icon"><svg width="32" height="22" viewBox="0 0 32 22"><path fill="#fff" d="M0 3h21v16H0zM22 9l10-6v16l-10-6z"/></svg></div>
  <h3>Security Service</h3>
  <p>Aliquam ullamcorper nisi ex, et ultricies quam congue sit amet. Mauris placerat dui sed mauris tristique pharetra. Proin porttitor sem mi, sit amet pulvinar magna euismod sed. <b>Read more</b></p>
</section>
<div class="abs rule" style="top:1011px"></div>

<section>
  <div class="abs gallery-head" style="left:132px"><span>Our vehicles</span><span class="more">»</span></div>
  <div class="abs thumbs" style="left:132px">
    <div class="thumb t-truck" role="img" aria-label="Red delivery vans parked at a depot"><span class="caption">Curabitur interdum</span></div>
    <div class="thumb t-truck2" role="img" aria-label="White semi truck at sunset"></div>
    <div class="thumb t-truck3" role="img" aria-label="Row of parked semi trucks"></div>
    <div class="thumb t-truck4" role="img" aria-label="Green truck cab on the road"></div>
    <div class="thumb t-truck5" role="img" aria-label="Blue and white trucks side by side"></div>
    <div class="thumb t-truck6" role="img" aria-label="Red tanker truck on a highway"></div>
  </div>
  <div class="abs gallery-head" style="left:629px"><span>Alarm systems</span><span class="tab-off">video systems</span><span class="more">»</span></div>
  <div class="abs thumbs" style="left:629px">
    <div class="thumb t-cam" role="img" aria-label="Wall mounted security camera"></div>
    <div class="thumb t-cam2" role="img" aria-label="Dome camera on a ceiling"></div>
    <div class="thumb t-cam3" role="img" aria-label="Indoor dome camera"></div>
    <div class="thumb t-cam4" role="img" aria-label="Outdoor dome camera on a wall"></div>
    <div class="thumb t-cam2" role="img" aria-label="Bullet camera on a building corner"></div>
    <div class="thumb t-cam5" role="img" aria-label="Small home security camera on a shelf"></div>
  </div>
</section>

<section class="abs band band-left feature">
  <h3 style="left:132px">MMJ trasnport &amp; Courier services</h3>
  <div class="photo ph-courier" style="left:132px" role="img" aria-label="Courier handing over a parcel for signature"></div>
  <p style="left:297px">Aliquam ullamcorper nisi ex, et ultricies quam congue sit amet. Aenean viverra quam id tellus tempor pretium. Suspendisse ac erat venenatis dui sagittis consequat non eu diam. Mauris at mattis libero. Donec eu metus leo. Ut imperdiet nisl molestie ante volutpat luctus. Mauris placerat dui sed mauris tristique pharetra. Proin porttitor sem mi, sit amet pulvinar magna euismod sed. <b>Read more</b></p>
</section>
<section class="abs band band-right feature">
  <h3 style="left:26px">Surveillance &amp; Security Services</h3>
  <div class="photo ph-monitor" style="left:26px" role="img" aria-label="Operator watching a wall of surveillance monitors"></div>
  <p style="left:192px">Aliquam ullamcorper nisi ex, et ultricies quam congue sit amet. Aenean viverra quam id tellus tempor pretium. Suspendisse ac erat venenatis dui sagittis consequat non eu diam. Mauris at mattis libero. Donec eu metus leo. Ut imperdiet nisl molestie ante volutpat luctus. Mauris placerat dui sed mauris tristique pharetra. Proin porttitor sem mi, sit amet pulvinar magna euismod sed. <b>Read more</b></p>
</section>

<section>
  <div class="abs badge-seal" aria-label="State license badge"></div>
  <div class="abs partner"><i></i>tallow unified</div>
  <div class="abs contact-info">
    <div class="addr">24 Building name, Street name, City - Zipcode</div>
    <div class="line">555.010.1548<span>|</span>info@harborcrestprotective.example</div>
  </div>
  <div class="abs phone-dot"><svg width="13" height="13" viewBox="0 0 24 24"><path fill="#fff" d="M6.6 10.8a15 15 0 0 0 6.6 6.6l2.2-2.2c.3-.3.7-.4 1-.2 1.1.4 2.3.6 3.6.6.6 0 1 .4 1 1V20c0 .6-.4 1-1 1A17 17 0 0 1 3 4c0-.6.4-1 1-1h3.5c.6 0 1 .4 1 1 0 1.3.2 2.5.6 3.6.1.3 0 .7-.2 1z"/></svg></div>
</section>

<div class="abs map" role="img" aria-label="Light grey world map showing the company location"></div>

<footer>
  <div class="abs footer"></div>
  <div class="abs f-nav" style="top:2049px">
    <div class="f-title">Navigation</div>
    <div class="cols">
      <ul><li>Home</li><li>About us</li><li>Our staff</li><li>MMJ trasnport &amp; Courier services</li><li>Our vehicles</li><li>Alarm systems</li></ul>
      <ul><li>video systems</li><li>video monitoring</li><li>private investigations</li><li>Surveillance audit</li><li>Compliance investigations</li><li>Contact us</li></ul>
    </div>
  </div>
  <div class="abs f-div" style="left:424px"></div>
  <div class="abs f-contact" style="top:2049px"><div class="f-title">Contact us</div></div>
  <form class="abs f-form">
    <div class="field" style="left:0;top:0;width:174px">Name</div>
    <div class="field" style="left:184px;top:0;width:174px">Email</div>
    <div class="field" style="left:0;top:39px;width:174px">Phone</div>
    <div class="field" style="left:184px;top:39px;width:174px">City</div>
    <div class="field" style="left:0;top:79px;width:358px">Message</div>
    <div class="submit">Submit</div>
  </form>
  <div class="abs f-div" style="left:887px"></div>
  <div class="abs copy">Copyright © 2016<br>Harbor Crest Protective solutions.<br>All Rights Reserved.</div>
  <div class="abs social"><i></i><i></i><i></i></div>
</footer>

</body>
</html>
```